Modern, traditional Catering Menu for hotel and conference centre

Modernization of Catering menu while still making this very legible and clear to all guests. Template required in Microsoft word document so that updates to menu items can be easily updated. Menu needs style relatable to hotel and conference centre in an area known for apples, farming and awe-inspiring landscape.

Target Market(s)

Conference and meeting groups,

Industry/Entity Type

Hospitality

Font styles to use
Serif
Script

Colors

Designer to choose colors to be used in the design.

Requirements
Must have
• Legible and clear headers and modern look.
• Microsoft word template to easily be able to make updates.
Nice to have
• Something unique related to apples and our logo

```html
<!DOCTYPE html>
<html lang="en">
<head>
<meta charset="utf-8">
<title>Crabapple Hill Inn – Event Essentials</title>
<link href="https://fonts.googleapis.com/css2?family=Crimson+Text:wght@400&family=Tinos:wght@400&family=Kaushan+Script&display=swap" rel="stylesheet">
<style>
  :root {
    --crimson: #bf2a4a;
    --crimson-deep: #b3213f;
    --ink: #1f1f1f;
    --rule: #4a3838;
    --paper: #ffffff;
    --backdrop: #e4e4e5;
    --gold: #d9a64e;
    --amber: #c9793a;
  }
  * { margin: 0; padding: 0; box-sizing: border-box; }
  html, body { width: 1200px; height: 1200px; overflow: hidden; }
  body { background: var(--backdrop); position: relative; }

  .sheet {
    position: absolute; left: 150px; top: 30px;
    width: 900px; height: 1140px;
    background: var(--paper);
    overflow: hidden;
  }
  .masthead { position: absolute; left: 0; top: 0; width: 900px; height: 215px; }
  .brand {
    position: absolute; right: 36px; top: 42px;
    font-family: "Crimson Text", serif; font-size: 50px; line-height: 1;
    color: #fff; text-align: right;
  }
  .brand-tagline {
    position: absolute; right: 37px; top: 98px;
    font-family: "Crimson Text", serif; font-size: 14px; color: #fff;
  }
  .section-title {
    position: absolute; left: 55px;
    font-family: "Kaushan Script", cursive; font-size: 38px;
    color: var(--crimson); line-height: 1;
  }
  .section-title.facility { top: 240px; }
  .section-title.essentials { top: 396px; }
  .title-rule {
    position: absolute; left: 59px; top: 442px; width: 336px; height: 3px;
    background: var(--rule);
  }
  .facility-copy {
    position: absolute; left: 56px; top: 292px; width: 810px;
    font-family: "Tinos", serif; font-size: 14px; line-height: 17.5px;
    color: var(--ink);
  }
  .essentials-list {
    position: absolute; left: 59px; top: 462px; list-style: none;
    font-family: "Tinos", serif; font-size: 14px; color: var(--ink);
  }
  .essentials-list li { height: 28.8px; line-height: 18px; }
  .terms {
    position: absolute; left: 0; width: 900px; top: 1094px; text-align: center;
    font-family: "Crimson Text", serif; font-size: 13.5px; color: var(--crimson);
  }
  .footer-band {
    position: absolute; left: 0; bottom: 0; width: 900px; height: 23px;
    background: var(--crimson-deep);
  }
</style>
</head>
<body>
  <main class="sheet">
    <svg class="masthead" viewBox="0 0 900 215" role="img" aria-label="Photograph of red apples in a wooden basket against a warm autumn field, blending into a crimson banner">
      <defs>
        <linearGradient id="banner-tone" x1="0" y1="0" x2="1" y2="0">
          <stop offset="0" stop-color="#b8823c"/>
          <stop offset="0.3" stop-color="#a3242e"/>
          <stop offset="0.5" stop-color="#d8904a"/>
          <stop offset="0.68" stop-color="#e0a55c"/>
          <stop offset="0.85" stop-color="#c94552"/>
          <stop offset="1" stop-color="#bf2a4a"/>
        </linearGradient>
        <linearGradient id="basket-tone" x1="0" y1="0" x2="0" y2="1">
          <stop offset="0" stop-color="#e9cfa0"/>
          <stop offset="1" stop-color="#f3e3c4"/>
        </linearGradient>
      </defs>
      <rect x="0" y="0" width="900" height="145" fill="url(#banner-tone)"/>
      <polygon points="40,145 452,145 440,185 380,210 36,162" fill="url(#basket-tone)"/>
    </svg>
    <div class="brand">Crabapple Hill Inn</div>
    <div class="brand-tagline">Hotel &amp; Conference Centre | Conference Groups Harvest Hall</div>

    <h2 class="section-title facility">Our Facility</h2>
    <p class="facility-copy">Crabapple Hill Inn is truly a landmark of hospitality in the Annapolis Valley of Nova Scotia with 101 Guest Rooms, 29 Seasonal Cabins (May - October) and Conference &amp; Event Centre with over 11,000 sq ft since established in 1972. The grounds sit nestled in one of the many beautiful apple orchards of Greenwich. Crabapple Hill Inn overlooks rolling landscapes of Cape Blomidon and the Minas Basin; part of the Bay of Fundy, featuring the world famous highest tides: truly an awe-inspiring view.</p>

    <h2 class="section-title essentials">Essentials for your event</h2>
    <div class="title-rule"></div>
    <ul class="essentials-list">
      <li>Professional Conference Centre</li>
      <li>Heritage Barn, a unique venue onsite offering limited catering</li>
      <li>Free parking</li>
      <li>Complimentary high-speed wireless internet</li>
      <li>Many popular attractions close by including several local wineries</li>
      <li>Parlour guestroom upgrade available to organizers and wedding couples</li>
      <li>Complimentary consultation with one of our Sales Team</li>
      <li>Menu tasting for two with our Chef for a nominal fee</li>
      <li>Guest rooms at a group rate (dependent on number of rooms rented for the occasion)</li>
      <li>Able to accommodate most dietary requirements, please inquire</li>
      <li>Children’s menus available</li>
      <li>Podium &amp; microphone available</li>
      <li>Guest book table, cake table, gift table</li>
      <li>Dance floor available at most venues</li>
      <li>Complimentary bar service (dependent on minimum sales)</li>
      <li>Complimentary cake cutting service, cake knife</li>
      <li>A selection of vases with votive candles for guest tables for a nominal rental fee</li>
      <li>White linen tablecloths and napkins</li>
      <li>Access to the breathtaking grounds for wedding photographs</li>
      <li>Seasonal fireside dining with a year round spectacular view of Cape Blomidon</li>
      <li>Avalon Quiet Lounge</li>
    </ul>

    <p class="terms">Effective: January 1, 2019. All prices are plus 16% gratuity plus applicable taxes and are subject to change.</p>
    <div class="footer-band"></div>
  </main>
</body>
</html>
```